Fern Lattice Table & Chair Rentals

We need a business card for a table and chair rental company. We rent tables and chairs for weddings, funerals, business events and parties. We want something that looks clean and elegant while not being too busy. We would like colors in the green and blue hues and avoiding anything orange. We want to make sure the font is large enough to be seen easily.

Target Market(s)

Wedding & Event Rentals

Industry/Entity Type

Events

Contact Information for Business Card

Fern Lattice, sales@fernlatticerentals.com, fernlatticerentals.com, 360-555-0182

Requirements
Must have
• Easy to read font
Should not have
• Orange anywhere in the design

```html
<!DOCTYPE html>
<html lang="en">
<head>
<meta charset="utf-8">
<title>Fern Lattice Table &amp; Chair Rentals – Business Card</title>
<link rel="stylesheet" href="https://fonts.googleapis.com/css2?family=Fira+Sans:wght@400;500&family=Arimo:wght@400;700&display=swap">
<style>
  :root {
    --backdrop: #e4e7e8;
    --card-green: #3a9d7a;
    --card-navy: #0e2433;
    --ink-navy: #0b1c28;
    --ink-green: #5cc39a;
  }
  * { box-sizing: border-box; margin: 0; padding: 0; }
  html, body {
    width: 1200px;
    height: 862px;
    overflow: hidden;
    background: var(--backdrop);
  }
  .stage {
    position: relative;
    width: 1200px;
    height: 862px;
    display: flex;
    justify-content: center;
    align-items: center;
    gap: 70px;
  }
  .card {
    position: relative;
    width: 370px;
    height: 640px;
    box-shadow: 0 12px 30px rgba(0,0,0,0.18);
  }
  .card--front {
    background: var(--card-green);
    color: var(--ink-navy);
    padding: 70px 30px 0 40px;
  }
  .card--back {
    background: var(--card-navy);
    color: var(--ink-green);
  }
  .brand-name {
    font-family: "Fira Sans", sans-serif;
    font-weight: 500;
    font-size: 44px;
    line-height: 1;
    letter-spacing: -0.5px;
  }
  .brand-tagline {
    font-family: "Fira Sans", sans-serif;
    font-weight: 400;
    font-size: 22px;
    margin-top: 10px;
  }
  .company-name {
    font-family: "Arimo", sans-serif;
    font-weight: 700;
    font-size: 19px;
    margin-top: 62px;
  }
  .contact-list {
    list-style: none;
    font-family: "Arimo", sans-serif;
    font-size: 17px;
    line-height: 1.6;
    margin-top: 46px;
  }
  .hours-list {
    list-style: none;
    font-family: "Arimo", sans-serif;
    font-size: 15px;
    line-height: 1.55;
    margin-top: 54px;
  }
  .back-brand {
    position: absolute;
    left: 40px;
    bottom: 70px;
  }
</style>
</head>
<body>
  <main class="stage">
    <section class="card card--front" aria-label="Business card front">
      <div class="brand-name">Fern Lattice</div>
      <div class="brand-tagline">Table and Chair Rentals</div>
      <div class="company-name">Fern Lattice Event Rentals, LLC</div>
      <ul class="contact-list">
        <li>360-555-0182</li>
        <li>www.fernlatticerentals.com</li>
        <li>sales@fernlatticerentals.com</li>
      </ul>
      <ul class="hours-list">
        <li>Mon-Fri: 8am to 6pm</li>
        <li>Saturday: 8am to 4pm</li>
        <li>Sunday: 9am to 1pm</li>
      </ul>
    </section>
    <section class="card card--back" aria-label="Business card back">
      <div class="back-brand">
        <div class="brand-name">Fern Lattice</div>
        <div class="brand-tagline">Table and Chair Rentals</div>
      </div>
    </section>
  </main>
</body>
</html>
```